Tutoring Site Hero Image Design

Updated Hero Concept for BrightHarborLessons.com

Create a hero that communicates “high quality, in-person private tutoring for all ages,” with warmth, credibility, and a real-life feel. The hero should move away from generic stock photography and better reflect the moments that make our service different: tutors meeting students where they are, one-on-one engagement, and a range of ages.

What the New Hero Should Convey
1. In-person, private, one-on-one support
This is the core differentiator, so the visual should feel intimate, focused, and real. Avoid anything that resembles online learning settings or learning-center classrooms.

2. Coverage of age ranges without clutter
We serve elementary through college. We do not need multiple students in the hero, but the chosen student should not skew strongly to one age group. Aim for a middle-ground age that feels inclusive, for example a middle schooler or early high schooler.

3. Realistic, authentic moments
Use photography that feels candid and warm. Natural light, home settings, kitchen tables, quiet study nooks, or library corners work well. Avoid staged stock looks, harsh lighting, or exaggerated classroom setups.

Design the hero at 2400 × 1200 px, with the focal point on the right side, safe area leaving room on the left for a stacked headline and form.

Images that I've shared as just thought starters and do not need to be used in the design.

Font styles to use
Sans Serif

Colors
0054AA
0677BA
7BADD7
CADEEF
E8F1F8
EB3D1F
EC4F4E
F09395
F8D3D4
FCEDEE
6B429C
8869AF
B7A5CE
E3DAEB
F3F0F8

```html
<!DOCTYPE html>
<html lang="en">
<head>
<meta charset="utf-8">
<title>Bright Harbor Lessons – Hero Concepts</title>
<link href="https://fonts.googleapis.com/css2?family=Poppins:wght@500;600;700&family=Lato:wght@400;700;900&display=swap" rel="stylesheet">
<style>
:root{
  --navy:#16217a;
  --navy-deep:#0e1866;
  --red:#e3202f;
  --sky:#8fd4f3;
  --sky-soft:#cadeef;
  --purple:#6b429c;
  --board:#d6d6d6;
  --paper:#ffffff;
  --mist:#f3f3f4;
  --ink:#222;
  --muted:#777;
}
*{box-sizing:border-box;margin:0;padding:0}
html,body{width:831px;height:1200px;overflow:hidden;background:var(--board);font-family:"Lato",sans-serif;color:var(--ink)}
.board{position:relative;width:831px;height:1200px}

/* ---------- concept card ---------- */
.concept-card{position:absolute;left:21px;top:21px;width:282px;height:318px;background:var(--paper)}
.concept-card .hero{position:absolute;left:21px;width:241px;height:131px;box-shadow:0 1px 4px rgba(0,0,0,.12)}
.concept-card .hero-a{top:17px}
.concept-card .hero-b{top:168px}

/* ---------- hero variants ---------- */
.hero{position:relative;overflow:hidden}
.hero-a{background:linear-gradient(90deg,#fff 55%,#fdf1f3 85%,#f7d9de 100%)}
.hero-a .photo{position:absolute;left:0;top:0;bottom:0;width:60%;
  background:linear-gradient(90deg,#b89472 0%,#d8bca0 35%,#efe2d3 70%,rgba(255,255,255,0) 100%)}
.hero-a .copy{position:absolute;left:57%;top:0;bottom:0;width:40%;display:flex;flex-direction:column;justify-content:center}
.hero-a h1{font-family:"Poppins",sans-serif;font-weight:600;color:var(--navy);line-height:1.12}
.hero-a h1 .hl{color:var(--red)}
.hero-b{background:linear-gradient(90deg,#0f1d7c 0%,#1c2587 38%,#5b3184 62%,#b2576f 82%,#d99a8a 100%)}
.hero-b .photo{position:absolute;right:0;top:0;bottom:0;width:48%;
  background:linear-gradient(90deg,rgba(120,60,120,0) 0%,rgba(176,110,100,.55) 45%,rgba(222,170,150,.7) 100%)}
.hero-b .copy{position:absolute;left:8.5%;top:0;bottom:0;width:48%;display:flex;flex-direction:column;justify-content:center}
.hero-b h1{font-family:"Poppins",sans-serif;font-weight:600;color:#fff;line-height:1.15}
.hero-b h1 .hl{background:var(--red);padding:0 1px}
.hero p{line-height:1.55}
.hero-a p{color:#666}
.hero-b p{color:#e8e8f4}
.hero .actions{display:flex;gap:4px}
.pill{display:inline-flex;align-items:center;justify-content:center;border-radius:20px;font-family:"Lato",sans-serif;font-weight:700;white-space:nowrap}
.pill.red{background:var(--red);color:#fff}
.pill.navy{background:var(--navy);color:#fff}
.pill.sky{background:var(--sky);color:var(--navy)}
.pill.outline{border:.6px solid var(--navy);color:var(--navy);background:#fff}
.pill.outline-sky{border:.6px solid var(--navy);background:var(--sky);color:var(--navy)}
.brand{font-family:"Lato",sans-serif;font-weight:900;color:var(--navy);display:flex;align-items:center;gap:2px;white-space:nowrap}
.brand .dot{width:5px;height:5px;border-radius:50%;background:var(--red);flex:none}

.concept-card .hero-a h1{font-size:8.4px}
.concept-card .hero p{font-size:2.6px;margin:4px 0 5px}
.concept-card .pill{font-size:2.8px;height:7px;padding:0 5px}
.concept-card .hero-a .brand{position:absolute;left:57%;top:14px;font-size:4.6px}
.concept-card .hero-b .brand{position:absolute;left:0;top:17px;background:#fff;padding:3px 8px 3px 22px;border-radius:0 10px 10px 0;font-size:4.6px}
.concept-card .hero-b h1{font-size:8px}
.concept-card .hero-b .copy{top:30px}

/* ---------- page mockups ---------- */
.page{position:absolute;top:21px;width:234px;height:1159px;background:var(--paper);display:flex;flex-direction:column;box-shadow:0 1px 3px rgba(0,0,0,.08)}
.page-one{left:325px}
.page-two{left:576px}
.page>section,.page>header,.page>footer{flex:none;position:relative}
.nav{height:14px;display:flex;align-items:center;padding:0 8px 0 22px;gap:6px;font-size:2.6px;color:#333}
.nav .brand{font-size:4px;margin-right:8px}
.nav .home{width:3.5px;height:3.5px;border-radius:50%;background:var(--navy)}
.nav .phone{display:flex;align-items:center;gap:1px;font-weight:700}
.page .hero{height:103px}
.page .hero-a h1{font-size:8.2px}
.page .hero-b h1{font-size:8px}
.page .hero-b .copy{width:52%;justify-content:flex-start;padding-top:25px;left:18px}
.page .hero p{font-size:2.3px;margin:4px 0 5px}
.page .pill{font-size:2.7px;height:7px;padding:0 5px}

.sec-title{font-family:"Lato",sans-serif;font-weight:700;font-size:5.4px;text-align:center;color:#222}
.sec-kicker{font-size:2.6px;color:var(--red);text-align:center;font-weight:700;margin-top:2px}

/* compare */
.compare{height:143px;padding-top:13px}
.compare-box{position:relative;margin:9px 22px 0;height:106px;background:#eef0f2;border-radius:4px}
.compare-box .lbl{position:absolute;top:6px;font-weight:700;font-size:4.4px}
.compare-card{position:absolute;top:14px;width:83px;height:81px;border-radius:3px;padding:3px}
.compare-card .ph{height:40px;border-radius:2px}
.compare-card h3{font-size:3.5px;font-weight:900;margin:4px 0 2px}
.compare-card p{font-size:2px;line-height:1.55}
.compare-card.them{left:5px;background:#fff;border:.6px solid #ddd}
.compare-card.them .ph{background:linear-gradient(135deg,#5f5f5f,#bcbcbc)}
.compare-card.us{right:5px;background:var(--navy);color:#fff;border:1.2px solid #3b54c9}
.compare-card.us .ph{background:linear-gradient(135deg,#5b7bb0,#c49e78)}
.vs{position:absolute;left:50%;top:52px;transform:translateX(-50%);font-weight:900;font-size:4.4px;color:#444}
.arrow-dot{position:absolute;top:50px;width:5px;height:5px;border-radius:50%;background:#e5e5e5;border:.4px solid #bbb}
.dots{position:absolute;bottom:3px;left:50%;transform:translateX(-50%);display:flex;gap:1.5px}
.dots i{width:1.5px;height:1.5px;border-radius:50%;background:#999}
.dots i:first-child{background:#222}

/* subjects */
.subjects{height:108px;background:var(--mist);padding-top:11px}
.subject-row{display:flex;gap:6px;margin:9px 22px 0}
.subject{flex:1;background:#fff;border-radius:3px;padding:5px 4px 4px;box-shadow:0 .5px 2px rgba(0,0,0,.1);position:relative}
.subject h4{font-size:2.8px;font-weight:700;margin-bottom:4px}
.subject .ico{position:absolute;right:4px;top:3px;width:8px;height:8px;border-radius:50%;background:var(--sky);border:1px solid #5aa6dd}
.list{list-style:none;font-size:2.6px;color:#444}
.list li{display:flex;align-items:center;gap:2px;margin-bottom:4px}
.tick{width:3px;height:3px;border-radius:50%;border:.5px solid #c77;flex:none}
.subject .pill{width:100%;height:7px;font-size:2.5px;margin-top:1px}
.center-btns{display:flex;justify-content:center;gap:4px}
.subjects .center-btns{margin-top:9px}
.subjects .pill{font-size:2.6px;height:7px;padding:0 5px}

/* locations */
.locations{height:144px;padding-top:12px}
.loc-grid{display:grid;grid-template-columns:repeat(4,1fr);gap:4px;margin:10px 22px 0}
.loc{height:45px;background:#f5f6f7;border-radius:2px;position:relative;display:flex;flex-direction:column;align-items:center;padding-top:7px}
.loc .circ{width:19px;height:19px;border-radius:50%}
.loc span{font-size:2.6px;margin-top:3px}
.loc .arr{position:absolute;right:3px;bottom:3px;font-size:3.5px;color:#5aa6dd}
.loc.all{background:var(--navy);color:#fff;align-items:flex-start;padding:7px 4px 0}
.loc.all svg{align-self:center}
.loc.all b{font-size:2.6px;align-self:center;margin-top:2px}
.loc.all small{font-size:2px;font-weight:700;margin-top:4px}
.loc.all .arr{color:#fff}

/* testimonials */
.testimonials{height:125px;padding-top:16px}
.t-left{position:absolute;left:22px;top:39px}
.t-left .kick{font-size:3.6px;letter-spacing:1.2px;font-weight:700;color:var(--red)}
.t-left h3{font-size:6px;font-weight:900;color:#333;line-height:1.4;margin-top:1px}
.t-stack{position:absolute;left:94px;top:16px;width:118px;height:72px}
.t-stack .back{position:absolute;inset:0;background:#fff;border-radius:3px;box-shadow:0 .5px 3px rgba(0,0,0,.15)}
.t-card{position:absolute;left:5px;right:0;top:0;bottom:2px;background:#fff;border-radius:3px;box-shadow:0 .5px 3px rgba(0,0,0,.15);padding:6px 6px}
.t-card h4{font-size:3.6px;font-weight:700}
.t-card small{font-size:1.8px;color:#777}
.acc{border-radius:1.5px;margin-top:3px;padding:2px 3px;font-size:2.4px;font-weight:700}
.acc.open{background:var(--navy);color:#fff;margin-top:4px}
.acc.open p{font-size:1.9px;font-weight:400;margin-top:3px;line-height:1.5}
.acc.closed{background:var(--sky);color:var(--navy)}
.t-nav{position:absolute;top:36px;width:6px;height:6px;border-radius:50%;background:#fff;box-shadow:0 .5px 2px rgba(0,0,0,.2)}
.testimonials .center-btns{position:absolute;left:0;right:0;top:101px}

/* expertise band */
.expertise{height:51px;margin:0 1px;background:linear-gradient(90deg,#6a2c86 0%,#8a2c6a 50%,#c8334a 100%);color:#fff;text-align:center;padding-top:9px}
.expertise h2{font-weight:700;font-size:8px;line-height:1.15}
.expertise p{font-size:2.4px;margin-top:4px;line-height:1.6;padding:0 40px}

/* confidence */
.confidence{height:115px;padding-top:10px}
.conf-card{position:absolute;left:22px;top:27px;width:72px;height:78px;border-radius:3px;background:var(--red);color:#fff;overflow:hidden}
.conf-card .ph{height:30px;background:linear-gradient(180deg,#b86a5a,#e3202f)}
.conf-card h3{font-size:5.4px;font-weight:900;padding:0 5px;line-height:1.05}
.conf-card p{font-size:2px;padding:2px 5px;line-height:1.5}
.feat-grid{position:absolute;left:98px;top:9px;width:114px;display:grid;grid-template-columns:1fr 1fr;gap:4px}
.feat{background:#fff;border-radius:3px;box-shadow:0 .5px 3px rgba(0,0,0,.14);padding:4px 3px;position:relative;height:47px}
.feat h5{font-size:2.5px;color:var(--red);font-weight:700;width:70%;line-height:1.3}
.feat .ico{position:absolute;right:3px;top:3px;width:6px;height:6px;border-radius:50%;background:var(--navy)}
.feat .list{font-size:1.9px;margin-top:3px}
.feat .list li{align-items:flex-start;margin-bottom:3px}

/* steps */
.steps{height:116px;padding-top:12px}
.step-row{display:flex;gap:6px;margin:10px 22px 0}
.step{flex:1;height:60px;border-radius:3px;background:#fff;box-shadow:0 .5px 3px rgba(0,0,0,.14);text-align:center;position:relative;padding-top:10px}
.step .tag{position:absolute;top:-2px;left:50%;transform:translateX(-50%);background:var(--sky);border-radius:6px;font-size:2.4px;padding:1px 5px;font-weight:700;color:var(--navy)}
.step .ico{width:10px;height:10px;margin:0 auto;border-radius:2px;background:var(--navy)}
.step h5{font-size:2.9px;color:var(--red);margin-top:5px}
.step p{font-size:1.9px;color:#666;line-height:1.5;padding:2px 4px}
.steps .center-btns{margin-top:10px}

/* blog */
.blog{height:105px;background:var(--mist);padding-top:12px}
.blog-row{display:flex;gap:6px;margin:9px 22px 0}
.post{flex:1;height:56px;border-radius:2px;position:relative;overflow:hidden}
.post.main{background:linear-gradient(160deg,#6b5a46,#4f7d4a 60%,#8d8368)}
.post.main .txt{position:absolute;left:3px;bottom:3px;color:#fff;font-size:2.2px;line-height:1.45}
.post.faint .txt{position:absolute;left:3px;bottom:6px;color:#e6e6e6;font-size:2px;line-height:1.5}
.blog .center-btns{margin-top:9px}

/* cta */
.cta{height:67px}
.cta-box{position:absolute;left:132px;top:14px;width:76px;height:38px;background:var(--red);border-radius:3px;color:#fff;text-align:center;padding-top:4px}
.cta-box h3{font-size:5.2px;font-weight:700}
.cta-box p{font-size:2.2px;line-height:1.5;margin:1px 6px 3px}
.cta-box .center-btns{gap:2px}
.cta-box .pill{font-size:2.4px;height:7px;padding:0 5px;border:.5px solid #fff}

/* footer */
.site-footer{height:66px;background:var(--navy);color:#fff}
.site-footer .brand{position:absolute;left:25px;top:16px;color:#fff;font-size:5.4px}
.site-footer .tag{position:absolute;left:25px;top:33px;font-size:2.6px;line-height:1.6;font-weight:700}
.f-col{position:absolute;top:15px;font-size:2.4px;line-height:1.7}
.f-col b{display:block;margin-bottom:3px}
.socials{display:flex;gap:3px;margin-top:3px}
.socials i{width:5px;height:5px;border-radius:50%;background:#fff}
.f-bar{position:absolute;left:0;right:0;bottom:0;height:8px;background:var(--navy-deep);font-size:2.1px;display:flex;align-items:center;padding:0 23px;gap:9px;color:#ccd}
.f-bar span:first-child{margin-right:auto}
</style>
</head>
<body>
<main class="board">

  <!-- hero concept card -->
  <article class="concept-card">
    <div class="hero hero-a">
      <div class="photo" role="img" aria-label="Warm home photo of a tutor and a young student reading together at a table"></div>
      <div class="brand"><span class="dot"></span>Bright Harbor Lessons</div>
      <div class="copy" style="padding-top:14px">
        <h1>Local Tutors.<br><span class="hl">1-on-1 Learning.</span><br>Real Results.</h1>
        <p>For over 20 years, Bright Harbor Lessons has introduced students and families in our communities to experienced, professional, independent tutors who offer individualized, student-centered support across all grades and subjects, from kindergarten through college.</p>
        <div class="actions"><span class="pill red">Get a Quote</span><span class="pill navy">Call (555) 204-8816</span></div>
      </div>
    </div>
    <div class="hero hero-b">
      <div class="photo" role="img" aria-label="Tutor leaning in to help a teen student write at a kitchen table"></div>
      <div class="brand"><span class="dot"></span>Bright Harbor Lessons</div>
      <div class="copy">
        <h1>Local Tutors. <span class="hl">1-on-1</span><br>Learning.Real Results.</h1>
        <p>For over 20 years, Bright Harbor Lessons has introduced students and families in our communities to experienced, professional, independent tutors who offer individualized, student-centered support across all grades and subjects, from kindergarten through college.</p>
        <div class="actions"><span class="pill red">Get a Quote</span><span class="pill navy">Call (555) 204-8816</span></div>
      </div>
    </div>
  </article>

  <!-- full page, concept A -->
  <div class="page page-one">
    <header class="nav">
      <div class="brand"><span class="dot"></span>Bright Harbor</div>
      <span class="home"></span><span>Tutoring Services ▾</span><span>Locations</span><span>Resources ▾</span><span>For Partners</span><span>For Tutors</span>
      <span class="phone"><svg width="3" height="3" viewBox="0 0 10 10"><path d="M2 0l2 2-1 2 3 3 2-1 2 2-2 2C4 10 0 6 0 2z" fill="#16217a"/></svg>(555) 204-8816</span>
    </header>
    <section class="hero hero-a">
      <div class="photo" role="img" aria-label="Warm home photo of a tutor and a young student reading together at a table"></div>
      <div class="copy" style="left:61%;width:36%">
        <h1>Local Tutors.<br><span class="hl">1-on-1 Learning.</span><br>Real Results.</h1>
        <p>For over 20 years, Bright Harbor Lessons has introduced students and families in our communities to experienced, professional, independent tutors who offer individualized, student-centered support across all grades and subjects, from kindergarten through college.</p>
        <div class="actions"><span class="pill red">Get a Quote</span><span class="pill navy">Call (555) 204-8816</span></div>
      </div>
    </section>
    <section class="compare">
      <h2 class="sec-title">Where Traditional Tutoring Misses the Mark</h2>
      <div class="compare-box">
        <span class="lbl" style="left:38px">THEM</span><span class="lbl" style="right:38px">US</span>
        <span class="arrow-dot" style="left:-2px"></span><span class="arrow-dot" style="right:-2px"></span>
        <div class="compare-card them"><div class="ph" role="img" aria-label="Black and white photo of a tired child at a laptop"></div><h3>Online-Only Tutoring</h3><p>It's no secret that over-reliance on virtual learning in recent years has led to real learning loss, but more screen time isn't the answer.</p></div>
        <span class="vs">VS</span>
        <div class="compare-card us"><div class="ph" role="img" aria-label="Tutor and student working side by side at home"></div><h3>In-Person, 1-On-1 Tutoring</h3><p>Students thrive when learning happens in real life. Families connect with a local, professional tutor who meets in person to provide focused, one-on-one support without screens or distractions.</p></div>
        <div class="dots"><i></i><i></i><i></i></div>
      </div>
    </section>
    <section class="subjects">
      <h2 class="sec-title">Personalized Learning Plans for Every Grade, Every Subject</h2>
      <div class="subject-row">
        <div class="subject"><h4>K12</h4><span class="ico"></span><ul class="list"><li><span class="tick"></span>Language Arts</li><li><span class="tick"></span>Mathematics</li><li><span class="tick"></span>Science</li><li><span class="tick"></span>Social Studies</li></ul><span class="pill sky">Explore K-12 Tutoring</span></div>
        <div class="subject"><h4>University &amp; College</h4><span class="ico"></span><ul class="list"><li><span class="tick"></span>Humanities</li><li><span class="tick"></span>Foreign Languages</li><li><span class="tick"></span>Computing</li><li><span class="tick"></span>Biology</li></ul><span class="pill sky">Explore Higher Ed Tutoring</span></div>
        <div class="subject"><h4>Test Prep</h4><span class="ico"></span><ul class="list"><li><span class="tick"></span>ACT</li><li><span class="tick"></span>SAT</li><li><span class="tick"></span>SSAT</li><li><span class="tick"></span>Private School Admissions</li></ul><span class="pill sky">Start your Exam Prep Now!</span></div>
      </div>
      <div class="center-btns"><span class="pill outline">View ALL Tutoring Services</span></div>
    </section>
    <section class="locations">
      <h2 class="sec-title">Private Home Lessons Delivered Coast to Coast</h2>
      <p class="sec-kicker">POPULAR LOCATIONS</p>
      <div class="loc-grid">
        <div class="loc"><div class="circ" role="img" aria-label="California city view" style="background:linear-gradient(#9bb8d6,#8b7a62)"></div><span>California</span><b class="arr">→</b></div>
        <div class="loc"><div class="circ" role="img" aria-label="New York skyline" style="background:linear-gradient(#c7d0da,#3f4650)"></div><span>New York</span><b class="arr">→</b></div>
        <div class="loc"><div class="circ" role="img" aria-label="Florida beach with palms" style="background:linear-gradient(#6aa7e0,#c9b48a)"></div><span>Florida</span><b class="arr">→</b></div>
        <div class="loc"><div class="circ" role="img" aria-label="Texas skyline at sunset" style="background:linear-gradient(#e06a8a,#c2562d)"></div><span>Texas</span><b class="arr">→</b></div>
        <div class="loc"><div class="circ" role="img" aria-label="Arizona desert at dusk" style="background:linear-gradient(#b9a6d3,#a2532c)"></div><span>Arizona</span><b class="arr">→</b></div>
        <div class="loc"><div class="circ" role="img" aria-label="Alabama river valley" style="background:linear-gradient(#9fc0e0,#56743f)"></div><span>Alabama</span><b class="arr">→</b></div>
        <div class="loc"><div class="circ" role="img" aria-label="Washington capitol building" style="background:linear-gradient(#3f8ad6,#e5c88a)"></div><span>Washington</span><b class="arr">→</b></div>
        <div class="loc all"><svg width="18" height="14" viewBox="0 0 36 28" fill="none" stroke="#fff" stroke-width="1.4"><path d="M2 10l8-6 10 2 12-4 2 10-6 12-14-2-10 2z"/><circle cx="20" cy="10" r="4"/><path d="M20 14v6"/></svg><b>We Are in 40+ States</b><small>Explore ALL<br>Locations</small><b class="arr">→</b></div>
      </div>
    </section>
    <section class="testimonials">
      <div class="t-left"><p class="kick">TESTIMONIALS</p><h3>Bright Harbor<br>Exceeded Every<br>Expectation</h3></div>
      <div class="t-stack">
        <div class="back"></div>
        <div class="t-card">
          <h4>Dana Whitfield</h4><small>Mother, High School Math Student</small>
          <div class="acc open">The Challenge<p>When my daughter entered high school in March, I knew a mid-year change of schools would be a challenge—especially in math.</p></div>
          <div class="acc closed">The Solution</div>
          <div class="acc closed">The Result</div>
        </div>
        <span class="t-nav" style="left:1px"></span><span class="t-nav" style="right:-3px"></span>
      </div>
      <div class="center-btns"><span class="pill outline">Get a Quote</span><span class="pill sky">Call (555) 204-8816</span></div>
    </section>
    <section class="expertise" role="img" aria-label="Purple to red banner over a soft study photo">
      <h2>20+ Years of Expertise. Proven Success.<br>Personalized Tutoring.</h2>
      <p>For over two decades, we've helped thousands of students achieve breakthrough results with customized, one-on-one tutoring – in person and at home.</p>
    </section>
    <section class="confidence">
      <div class="conf-card"><div class="ph" role="img" aria-label="Student writing notes at a desk"></div><h3>Confidence. Curiosity.<br>Real Results.</h3><p>At Bright Harbor Lessons, we believe one-on-one connections make all the difference. Students work with experienced, professional tutors who focus on building confidence, sparking curiosity, and driving measurable improvements in just weeks.</p></div>
      <div class="feat-grid">
        <div class="feat"><h5>Local Support You Control</h5><span class="ico"></span><ul class="list"><li><span class="tick"></span>Choose the location, at home or wherever works best</li><li><span class="tick"></span>Flexible scheduling to fit busy calendars</li><li><span class="tick"></span>Tutors from your area, each showing subject expertise</li></ul></div>
        <div class="feat"><h5>Learning Designed Around Your Child</h5><span class="ico"></span><ul class="list"><li><span class="tick"></span>Lessons are customized to your child's learning style and pace</li><li><span class="tick"></span>Areas of need are met with the right tools</li><li><span class="tick"></span>Dedicated support to give your child the attention they need</li></ul></div>
        <div class="feat"><h5>Comprehensive Tutoring for Every Stage</h5><span class="ico"></span><ul class="list"><li><span class="tick"></span>Supporting elementary, middle, and high school students</li><li><span class="tick"></span>Specialized test prep for SAT, GRE, and ASVAB success</li><li><span class="tick"></span>College tutoring to excel in advanced courses</li></ul></div>
        <div class="feat"><h5>A Full Support System for Students and Parents</h5><span class="ico"></span><ul class="list"><li><span class="tick"></span>Ongoing guidance to keep students on track</li><li><span class="tick"></span>Clear communication to keep parents informed</li><li><span class="tick"></span>Expert feedback to ensure consistent progress</li></ul></div>
      </div>
    </section>
    <section class="steps">
      <h2 class="sec-title">Find your Perfect Tutor in 3 Steps</h2>
      <div class="step-row">
        <div class="step"><span class="tag">STEP 1</span><div class="ico"></div><h5>Share Learning Goals</h5><p>Tell us a little info about the student's learning goals, challenges, and ideal schedule. It only takes a few minutes.</p></div>
        <div class="step"><span class="tag">STEP 2</span><div class="ico"></div><h5>We Build a Student Profile</h5><p>Your information is turned into a tailored profile that highlights all your needs, so it's ready for the right tutor.</p></div>
        <div class="step"><span class="tag">STEP 3</span><div class="ico"></div><h5>Meet Your Tutor</h5><p>We connect your profile to a qualified tutor. Once the tutor accepts, you'll connect directly &amp; sessions begin.</p></div>
      </div>
      <div class="center-btns"><span class="pill outline">Get a Quote</span><span class="pill red">Call (555) 204-8816</span></div>
    </section>
    <section class="blog">
      <h2 class="sec-title">Strategies and Insights for Better Learning</h2>
      <div class="blog-row">
        <div class="post main" role="img" aria-label="Student in green sweater studying at home"><div class="txt">NOVEMBER 22, 2025<br><b>School Support vs Private Tutoring: A Parent's Guide</b><br>School Support<br><u>READ MORE</u></div></div>
        <div class="post faint"><div class="txt">NOVEMBER 18, 2025<br>Study Habits That Last</div></div>
        <div class="post faint"><div class="txt">NOVEMBER 10, 2025<br>Test Day Confidence Tips</div></div>
      </div>
      <div class="center-btns"><span class="pill sky">Call (555) 204-8816</span><span class="pill red">Explore Our Blog</span></div>
    </section>
    <section class="cta">
      <div class="cta-box"><h3>Take the First Step</h3><p>Kickstart your child's success story. Call us now and see improvements within weeks.</p><div class="center-btns"><span class="pill red">Get a Quote</span><span class="pill sky">Call (555) 204-8816</span></div></div>
    </section>
    <footer class="site-footer">
      <div class="brand"><span class="dot" style="background:#fff"></span>Bright Harbor Lessons</div>
      <p class="tag">Watch Your Student Thrive<br>with In-home, Personalized Tutoring</p>
      <div class="f-col" style="left:135px"><b>Navigation</b>Tutoring Services<br>Locations<br>About Us<br>Tutor Log In</div>
      <div class="f-col" style="left:172px"><b>Contact</b>☎ (555) 204-8816<div class="socials"><i></i><i></i><i></i><i></i></div></div>
      <div class="f-bar"><span>© 2002-2025 Bright Harbor Lessons</span><span>Privacy Policy</span><span>Terms of Use</span><span>Terms of Service</span></div>
    </footer>
  </div>

  <!-- full page, concept B -->
  <div class="page page-two">
    <header class="nav">
      <div class="brand"><span class="dot"></span>Bright Harbor</div>
      <span class="home"></span><span>Tutoring Services ▾</span><span>Locations</span><span>Resources ▾</span><span>For Partners</span><span>For Tutors</span>
      <span class="phone"><svg width="3" height="3" viewBox="0 0 10 10"><path d="M2 0l2 2-1 2 3 3 2-1 2 2-2 2C4 10 0 6 0 2z" fill="#16217a"/></svg>(555) 204-8816</span>
    </header>
    <section class="hero hero-b">
      <div class="photo" role="img" aria-label="Tutor leaning in to help a teen student write at a kitchen table"></div>
      <div class="copy">
        <h1>Local Tutors. <span class="hl">1-on-1</span><br>Learning.Real Results.</h1>
        <p>For over 20 years, Bright Harbor Lessons has introduced students and families in our communities to experienced, professional, independent tutors who offer individualized, student-centered support across all grades and subjects, from kindergarten through college.</p>
        <div class="actions"><span class="pill red">Get a Quote</span><span class="pill navy">Call (555) 204-8816</span></div>
      </div>
    </section>
    <section class="compare">
      <h2 class="sec-title">Where Traditional Tutoring Misses the Mark</h2>
      <div class="compare-box">
        <span class="lbl" style="left:38px">THEM</span><span class="lbl" style="right:38px">US</span>
        <span class="arrow-dot" style="left:-2px"></span><span class="arrow-dot" style="right:-2px"></span>
        <div class="compare-card them"><div class="ph" role="img" aria-label="Black and white photo of a tired child at a laptop"></div><h3>Online-Only Tutoring</h3><p>It's no secret that over-reliance on virtual learning in recent years has led to real learning loss, but more screen time isn't the answer.</p></div>
        <span class="vs">VS</span>
        <div class="compare-card us"><div class="ph" role="img" aria-label="Tutor and student working side by side at home"></div><h3>In-Person, 1-On-1 Tutoring</h3><p>Students thrive when learning happens in real life. Families connect with a local, professional tutor who meets in person to provide focused, one-on-one support without screens or distractions.</p></div>
        <div class="dots"><i></i><i></i><i></i></div>
      </div>
    </section>
    <section class="subjects">
      <h2 class="sec-title">Personalized Learning Plans for Every Grade, Every Subject</h2>
      <div class="subject-row">
        <div class="subject"><h4>K12</h4><span class="ico"></span><ul class="list"><li><span class="tick"></span>Language Arts</li><li><span class="tick"></span>Mathematics</li><li><span class="tick"></span>Science</li><li><span class="tick"></span>Social Studies</li></ul><span class="pill sky">Explore K-12 Tutoring</span></div>
        <div class="subject"><h4>University &amp; College</h4><span class="ico"></span><ul class="list"><li><span class="tick"></span>Humanities</li><li><span class="tick"></span>Foreign Languages</li><li><span class="tick"></span>Computing</li><li><span class="tick"></span>Biology</li></ul><span class="pill sky">Explore Higher Ed Tutoring</span></div>
        <div class="subject"><h4>Test Prep</h4><span class="ico"></span><ul class="list"><li><span class="tick"></span>ACT</li><li><span class="tick"></span>SAT</li><li><span class="tick"></span>SSAT</li><li><span class="tick"></span>Private School Admissions</li></ul><span class="pill sky">Start your Exam Prep Now!</span></div>
      </div>
      <div class="center-btns"><span class="pill outline">View ALL Tutoring Services</span></div>
    </section>
    <section class="locations">
      <h2 class="sec-title">Private Home Lessons Delivered Coast to Coast</h2>
      <p class="sec-kicker">POPULAR LOCATIONS</p>
      <div class="loc-grid">
        <div class="loc"><div class="circ" role="img" aria-label="California city view" style="background:linear-gradient(#9bb8d6,#8b7a62)"></div><span>California</span><b class="arr">→</b></div>
        <div class="loc"><div class="circ" role="img" aria-label="New York skyline" style="background:linear-gradient(#c7d0da,#3f4650)"></div><span>New York</span><b class="arr">→</b></div>
        <div class="loc"><div class="circ" role="img" aria-label="Florida beach with palms" style="background:linear-gradient(#6aa7e0,#c9b48a)"></div><span>Florida</span><b class="arr">→</b></div>
        <div class="loc"><div class="circ" role="img" aria-label="Texas skyline at sunset" style="background:linear-gradient(#e06a8a,#c2562d)"></div><span>Texas</span><b class="arr">→</b></div>
        <div class="loc"><div class="circ" role="img" aria-label="Arizona desert at dusk" style="background:linear-gradient(#b9a6d3,#a2532c)"></div><span>Arizona</span><b class="arr">→</b></div>
        <div class="loc"><div class="circ" role="img" aria-label="Alabama river valley" style="background:linear-gradient(#9fc0e0,#56743f)"></div><span>Alabama</span><b class="arr">→</b></div>
        <div class="loc"><div class="circ" role="img" aria-label="Washington capitol building" style="background:linear-gradient(#3f8ad6,#e5c88a)"></div><span>Washington</span><b class="arr">→</b></div>
        <div class="loc all"><svg width="18" height="14" viewBox="0 0 36 28" fill="none" stroke="#fff" stroke-width="1.4"><path d="M2 10l8-6 10 2 12-4 2 10-6 12-14-2-10 2z"/><circle cx="20" cy="10" r="4"/><path d="M20 14v6"/></svg><b>We Are in 40+ States</b><small>Explore ALL<br>Locations</small><b class="arr">→</b></div>
      </div>
    </section>
    <section class="testimonials">
      <div class="t-left"><p class="kick">TESTIMONIALS</p><h3>Bright Harbor<br>Exceeded Every<br>Expectation</h3></div>
      <div class="t-stack">
        <div class="back"></div>
        <div class="t-card">
          <h4>Dana Whitfield</h4><small>Mother, High School Math Student</small>
          <div class="acc open">The Challenge<p>When my daughter entered high school in March, I knew a mid-year change of schools would be a challenge—especially in math.</p></div>
          <div class="acc closed">The Solution</div>
          <div class="acc closed">The Result</div>
        </div>
        <span class="t-nav" style="left:1px"></span><span class="t-nav" style="right:-3px"></span>
      </div>
      <div class="center-btns"><span class="pill outline">Get a Quote</span><span class="pill sky">Call (555) 204-8816</span></div>
    </section>
    <section class="expertise" role="img" aria-label="Purple to red banner over a soft study photo">
      <h2>20+ Years of Expertise. Proven Success.<br>Personalized Tutoring.</h2>
      <p>For over two decades, we've helped thousands of students achieve breakthrough results with customized, one-on-one tutoring – in person and at home.</p>
    </section>
    <section class="confidence">
      <div class="conf-card"><div class="ph" role="img" aria-label="Student writing notes at a desk"></div><h3>Confidence. Curiosity.<br>Real Results.</h3><p>At Bright Harbor Lessons, we believe one-on-one connections make all the difference. Students work with experienced, professional tutors who focus on building confidence, sparking curiosity, and driving measurable improvements in just weeks.</p></div>
      <div class="feat-grid">
        <div class="feat"><h5>Local Support You Control</h5><span class="ico"></span><ul class="list"><li><span class="tick"></span>Choose the location, at home or wherever works best</li><li><span class="tick"></span>Flexible scheduling to fit busy calendars</li><li><span class="tick"></span>Tutors from your area, each showing subject expertise</li></ul></div>
        <div class="feat"><h5>Learning Designed Around Your Child</h5><span class="ico"></span><ul class="list"><li><span class="tick"></span>Lessons are customized to your child's learning style and pace</li><li><span class="tick"></span>Areas of need are met with the right tools</li><li><span class="tick"></span>Dedicated support to give your child the attention they need</li></ul></div>
        <div class="feat"><h5>Comprehensive Tutoring for Every Stage</h5><span class="ico"></span><ul class="list"><li><span class="tick"></span>Supporting elementary, middle, and high school students</li><li><span class="tick"></span>Specialized test prep for SAT, GRE, and ASVAB success</li><li><span class="tick"></span>College tutoring to excel in advanced courses</li></ul></div>
        <div class="feat"><h5>A Full Support System for Students and Parents</h5><span class="ico"></span><ul class="list"><li><span class="tick"></span>Ongoing guidance to keep students on track</li><li><span class="tick"></span>Clear communication to keep parents informed</li><li><span class="tick"></span>Expert feedback to ensure consistent progress</li></ul></div>
      </div>
    </section>
    <section class="steps">
      <h2 class="sec-title">Find your Perfect Tutor in 3 Steps</h2>
      <div class="step-row">
        <div class="step"><span class="tag">STEP 1</span><div class="ico"></div><h5>Share Learning Goals</h5><p>Tell us a little info about the student's learning goals, challenges, and ideal schedule. It only takes a few minutes.</p></div>
        <div class="step"><span class="tag">STEP 2</span><div class="ico"></div><h5>We Build a Student Profile</h5><p>Your information is turned into a tailored profile that highlights all your needs, so it's ready for the right tutor.</p></div>
        <div class="step"><span class="tag">STEP 3</span><div class="ico"></div><h5>Meet Your Tutor</h5><p>We connect your profile to a qualified tutor. Once the tutor accepts, you'll connect directly &amp; sessions begin.</p></div>
      </div>
      <div class="center-btns"><span class="pill outline">Get a Quote</span><span class="pill red">Call (555) 204-8816</span></div>
    </section>
    <section class="blog">
      <h2 class="sec-title">Strategies and Insights for Better Learning</h2>
      <div class="blog-row">
        <div class="post main" role="img" aria-label="Student in green sweater studying at home"><div class="txt">NOVEMBER 22, 2025<br><b>School Support vs Private Tutoring: A Parent's Guide</b><br>School Support<br><u>READ MORE</u></div></div>
        <div class="post faint"><div class="txt">NOVEMBER 18, 2025<br>Study Habits That Last</div></div>
        <div class="post faint"><div class="txt">NOVEMBER 10, 2025<br>Test Day Confidence Tips</div></div>
      </div>
      <div class="center-btns"><span class="pill sky">Call (555) 204-8816</span><span class="pill red">Explore Our Blog</span></div>
    </section>
    <section class="cta">
      <div class="cta-box"><h3>Take the First Step</h3><p>Kickstart your child's success story. Call us now and see improvements within weeks.</p><div class="center-btns"><span class="pill red">Get a Quote</span><span class="pill sky">Call (555) 204-8816</span></div></div>
    </section>
    <footer class="site-footer">
      <div class="brand"><span class="dot" style="background:#fff"></span>Bright Harbor Lessons</div>
      <p class="tag">Watch Your Student Thrive<br>with In-home, Personalized Tutoring</p>
      <div class="f-col" style="left:135px"><b>Navigation</b>Tutoring Services<br>Locations<br>About Us<br>Tutor Log In</div>
      <div class="f-col" style="left:172px"><b>Contact</b>☎ (555) 204-8816<div class="socials"><i></i><i></i><i></i><i></i></div></div>
      <div class="f-bar"><span>© 2002-2025 Bright Harbor Lessons</span><span>Privacy Policy</span><span>Terms of Use</span><span>Terms of Service</span></div>
    </footer>
  </div>

</main>
</body>
</html>
```